Business card design Needed for new logo / Construction business, home extensions and new builds

We need a business card design using our new logo files which i will attach to this project :)

We are a small construction business specialising in home extensions, new builds and property development. We are very ambitious and would appreciate professional and elegant designs for our new business card.

Very serious about using the services on MakerQuarry and recently acquired our new logo from here :)

Please get involved, i will feedback when i can as i am very busy but can respond daily, thanks

Target Market(s)

People that want to build onto their houses, new building developments or adding too their existing property

Industry/Entity Type

Construction

Contact Information for Business Card

Renwick Tolliver Construction, Lionel Ashby (Managing Director), Tel 07822254961, email - info@renwick-tolliver, www.renwick-tolliver.co.uk

Colors

Designer to choose colors to be used in the design.

Requirements
Must have
• I like a deep grey on the back please. A lot of you have provided black from and back, try mixing things up a little. The black looks cool 😎 Thanks

```html
<!DOCTYPE html>
<html lang="en">
<head>
<meta charset="utf-8">
<title>Renwick Tolliver Construction – Business Card</title>
<link rel="stylesheet" href="https://fonts.googleapis.com/css2?family=Cinzel:wght@600&family=Poppins:wght@400&display=swap">
<style>
  :root {
    --backdrop: #535353;
    --gold-deep: #bb7a10;
    --gold-light: #fdd98c;
    --silver-light: #f4f4f4;
    --silver-mid: #c9c9c9;
    --silver-dark: #9a9a9a;
    --ink: #111111;
    --card-back: #1b1b1b;
    --brand-gold: #d8a73a;
    --edge: #0d0d0d;
  }
  html, body {
    margin: 0;
    padding: 0;
    width: 1075px;
    height: 1200px;
    overflow: hidden;
    background: var(--backdrop);
  }
  .canvas {
    position: relative;
    width: 1075px;
    height: 1200px;
  }
  .card {
    position: absolute;
    border-radius: 26px;
    overflow: hidden;
    box-shadow: 3px 4px 0 var(--edge), 4px 6px 8px rgba(0,0,0,0.35);
  }
  .card--front {
    left: 209px;
    top: 189px;
    width: 659px;
    height: 391px;
    background: linear-gradient(180deg, var(--gold-deep) 0%, #d9a242 25%, var(--gold-light) 50%, #d9a242 75%, var(--gold-deep) 100%);
  }
  .card--back {
    left: 207px;
    top: 638px;
    width: 663px;
    height: 393px;
    background: var(--card-back);
  }
  .silver-panel {
    position: absolute;
    right: 0;
    top: 0;
    width: 171px;
    height: 100%;
    background: linear-gradient(180deg, var(--silver-dark) 0%, var(--silver-light) 45%, var(--silver-mid) 75%, var(--silver-dark) 100%);
  }
  .holder {
    position: absolute;
    left: 29px;
    top: 62px;
    color: var(--ink);
  }
  .holder__name {
    margin: 0;
    font-family: "Cinzel", serif;
    font-weight: 600;
    font-size: 23px;
    line-height: 26px;
    letter-spacing: 0.2px;
  }
  .holder__role {
    margin: 0;
    font-family: "Poppins", sans-serif;
    font-size: 18.5px;
    line-height: 22px;
  }
  .address, .contacts {
    position: absolute;
    left: 29px;
    margin: 0;
    padding: 0;
    list-style: none;
    font-family: "Poppins", sans-serif;
    font-size: 18.5px;
    line-height: 23.5px;
    color: var(--ink);
  }
  .address { top: 157px; font-style: normal; }
  .contacts { top: 275px; }
  .contacts li {
    display: flex;
    align-items: center;
    gap: 5px;
  }
  .contacts svg {
    width: 18px;
    height: 18px;
    flex: none;
  }
  .brand {
    position: absolute;
    left: 0;
    right: 0;
    top: 150px;
    text-align: center;
  }
  .brand__mark {
    display: block;
    width: 34px;
    height: 34px;
    margin: 0 auto 28px;
    background: var(--brand-gold);
  }
  .brand__name {
    margin: 0;
    font-family: "Cinzel", serif;
    font-weight: 600;
    font-size: 31px;
    line-height: 38px;
    letter-spacing: 1px;
    color: var(--brand-gold);
  }
</style>
</head>
<body>
<main class="canvas">
  <section class="card card--front" aria-label="Business card front">
    <div class="silver-panel"></div>
    <div class="holder">
      <h1 class="holder__name">DORIAN WEXLEY</h1>
      <p class="holder__role">Managing Director</p>
    </div>
    <address class="address">421, Address line<br>goes here 45452,<br>Country Name</address>
    <ul class="contacts">
      <li>
        <svg viewBox="0 0 24 24" aria-hidden="true"><path fill="#111" d="M6.6 10.8a15 15 0 0 0 6.6 6.6l2.2-2.2a1 1 0 0 1 1-.25 11.4 11.4 0 0 0 3.6.57 1 1 0 0 1 1 1V20a1 1 0 0 1-1 1A17 17 0 0 1 3 4a1 1 0 0 1 1-1h3.5a1 1 0 0 1 1 1c0 1.25.2 2.45.57 3.57a1 1 0 0 1-.25 1z"/></svg>
        044-610 382 574
      </li>
      <li>
        <svg viewBox="0 0 24 24" aria-hidden="true"><path fill="#111" d="M2 5h20v14H2z"/><path fill="none" stroke="#fdd98c" stroke-width="1.6" d="M2.5 5.5 12 13l9.5-7.5M2.5 18.5l7-6.5M21.5 18.5l-7-6.5"/></svg>
        info@sitemail.com
      </li>
      <li>
        <svg viewBox="0 0 24 24" aria-hidden="true"><g fill="none" stroke="#111" stroke-width="2"><circle cx="12" cy="12" r="9"/><ellipse cx="12" cy="12" rx="4" ry="9"/><path d="M3 12h18M5 7h14M5 17h14"/></g></svg>
        www.yoursitehere.com
      </li>
    </ul>
  </section>

  <section class="card card--back" aria-label="Business card back">
    <div class="brand">
      <span class="brand__mark" aria-hidden="true"></span>
      <p class="brand__name">RENWICK TOLLIVER<br>CONSTRUCTION</p>
    </div>
  </section>
</main>
</body>
</html>
```